I have a logo and need to design the business card and stationery.
Updates

The uploaded logo image named as GREYMARSH CONSTRUCTION which is to be replaced to GREYMARSH CONTRACTS. Kindly add below details and submit the designs- Company name- Greymarsh Engineering Contracts LLP Name & Post- Kelvan Joshi (Designated Partner) Address- Block No.317, Wing C, Tulvo Trade Court, Manek Pural Road, Ruparel Industrial Estate, Goregaon(E), Mumbai - 400 063 Contact- +91 97415 60382 Email- kelvanjoshi@mailbrook.example Website- www.greymarshcontracts.example Contact for Letterhead- +91-22-28754193

Hi Tovin Rahul, We are liking your Design #28860835. We have suggested some changes which are mentioned in feedback. Kindly revert with it asap to finalize this design.

Colors

Designer to choose colors to be used in the design.

```html
<!DOCTYPE html>
<html lang="en">
<head>
<meta charset="utf-8">
<title>Greymarsh Contracts Letterhead</title>
<link rel="stylesheet" href="https://fonts.googleapis.com/css2?family=Arimo:wght@400;700&family=Mulish:wght@700;800&display=swap">
<style>
  :root {
    --backdrop: #cfcfcf;
    --paper: #fbfbfc;
    --ink: #555659;
    --ink-soft: #6b6c6f;
    --rule: #7a7b7e;
    --band-dark: #2f3033;
    --band-grey: #76777a;
  }
  html, body {
    margin: 0;
    padding: 0;
    width: 1200px;
    height: 1079px;
    overflow: hidden;
    background: var(--backdrop);
  }
  .letterhead {
    position: absolute;
    left: 268px;
    top: 70px;
    width: 665px;
    height: 940px;
    background: var(--paper);
    overflow: hidden;
    font-family: "Arimo", Arial, sans-serif;
    color: var(--ink);
  }
  .brand-mark {
    position: absolute;
    left: 107px;
    top: 43px;
    width: 44px;
    height: 44px;
    background: var(--band-dark);
  }
  .brand-name {
    position: absolute;
    left: 59px;
    top: 92px;
    width: 146px;
    margin: 0;
    font-family: "Mulish", sans-serif;
    font-weight: 800;
    color: var(--band-dark);
    line-height: 1;
    white-space: nowrap;
  }
  .brand-name .line-main {
    display: block;
    font-size: 16px;
    letter-spacing: 0.3px;
  }
  .brand-name .line-sub {
    display: block;
    margin-top: 2px;
    font-size: 8px;
    letter-spacing: 8.3px;
  }
  .divider {
    position: absolute;
    top: 71px;
    width: 1px;
    height: 45px;
    background: var(--rule);
  }
  .divider.first { left: 228px; }
  .divider.second { left: 434px; }
  .address {
    position: absolute;
    left: 251px;
    top: 67px;
    margin: 0;
    font-size: 10px;
    line-height: 12.1px;
    color: var(--ink-soft);
    font-style: normal;
    white-space: nowrap;
  }
  .contacts {
    position: absolute;
    left: 455px;
    top: 74px;
    margin: 0;
    padding: 0;
    list-style: none;
    font-size: 10px;
    line-height: 14.2px;
    color: var(--ink-soft);
  }
  .contacts li {
    display: flex;
    align-items: center;
    gap: 6px;
    white-space: nowrap;
  }
  .contacts svg { width: 8px; height: 8px; fill: var(--band-dark); flex: none; }
  .header-rule {
    position: absolute;
    left: 56px;
    top: 123px;
    width: 552px;
    height: 1px;
    background: var(--rule);
  }
  .greeting {
    position: absolute;
    left: 60px;
    top: 289px;
    margin: 0;
    font-family: "Mulish", sans-serif;
    font-weight: 700;
    font-size: 15.4px;
    color: var(--ink);
  }
  .body-copy {
    position: absolute;
    left: 59px;
    top: 333px;
    width: 548px;
  }
  .body-copy p {
    margin: 0 0 11.5px;
    font-size: 11.1px;
    line-height: 13.7px;
  }
  .closing {
    position: absolute;
    left: 60px;
    top: 614px;
    margin: 0;
    font-family: "Mulish", sans-serif;
    font-weight: 700;
    font-size: 8.6px;
    color: var(--ink);
  }
  .signature {
    position: absolute;
    left: 60px;
    top: 654px;
    width: 108px;
    height: 33px;
    background: linear-gradient(90deg, rgba(85,86,89,0.28), rgba(85,86,89,0.12));
    border-radius: 16px;
  }
  .footer-band {
    position: absolute;
    left: 0;
    bottom: 0;
    width: 665px;
    height: 66px;
    background: linear-gradient(180deg, var(--paper) 0%, var(--band-grey) 35%, var(--band-dark) 70%);
  }
</style>
</head>
<body>
  <main class="letterhead">
    <div class="brand-mark"></div>
    <p class="brand-name"><span class="line-main">GREYMARSH</span><span class="line-sub">CONTRACTS</span></p>
    <div class="divider first"></div>
    <address class="address">
      Block No.317, Wing C<br>
      Tulvo Trade Court, Manek Pural Road<br>
      Ruparel Industrial Estate<br>
      Goregaon(E), Mumbai - 400 063
    </address>
    <div class="divider second"></div>
    <ul class="contacts">
      <li>
        <svg viewBox="0 0 10 10"><path d="M2 0.5 L3.6 2.6 L2.8 3.6 C3.4 5 4.9 6.5 6.4 7.2 L7.4 6.4 L9.5 8 L8.3 9.5 C4.5 9.2 0.8 5.5 0.5 1.7 Z"/></svg>
        +91-22-28754193
      </li>
      <li>
        <svg viewBox="0 0 10 10"><path d="M0 2 H10 V8 H0 Z M0.6 2.4 L5 5.6 L9.4 2.4" stroke="#fbfbfc" stroke-width="0.8"/></svg>
        kelvanjoshi@mailbrook.example
      </li>
      <li>
        <svg viewBox="0 0 10 10"><circle cx="5" cy="5" r="4.8"/><path d="M0.5 5 H9.5 M5 0.3 C3 3 3 7 5 9.7 M5 0.3 C7 3 7 7 5 9.7" stroke="#fbfbfc" stroke-width="0.7" fill="none"/></svg>
        www.greymarshcontracts.example
      </li>
    </ul>
    <div class="header-rule"></div>

    <h1 class="greeting">Dear Mr. Smith,</h1>

    <section class="body-copy">
      <p>Lorem ipsum dolor sit amet, consectetuer adipiscing elit, sed diam nonmmy nibh euismod tincidunt ut laoreet dolore magna aliquam erat volutpat. Ut wisi enim ad minim veniam, quis nostrud exerci tationmcorper suscipit lobortis nisl ut aliquip ex ea commodo consequat. Duis autem vel eum iriure dolor in hendrerit in vulputate velit esse molestie consequat, vel illum dolore eu feugiat</p>
      <p>Rorem ipsum dolor sit amet, consectetuer adipiscing elit, sed diam nonmmy nibh euismod tincidunt ut laoreet dolore magna aliquam erat volutpat. Ut wisi enim ad minim veniam, quis nostrud exerci tationmcorper suscipit lobortis nisl ut aliquip ex ea commodo consequat. Duis autem vel eum iriure dolor in hendrerit in vulputate velit esse molest</p>
      <p>Dorem ipsum dolor sit amet, consectetuer adipiscing elit, sed diam nonmmy nibh euismod tincidunt ut laoreet dolore magna aliquam erat volutpat. Ut wisi enim ad minim veniam, quis nostrud exerci tationmcorper suscipit lobortis nisl ut aliquip ex ea commodo consequat. Duis autem vel eum iriure dolor in hendrerit in suscipit lobortis nisl ut aliquip ex ea commodo consequat. Duis autem vel eum iriure dolor in hendrerit in vulputate velit esse molestie consequat, vel illum</p>
      <p>Sorem ipsum dolor sit amet, consectetuer adipiscing elit, sed diam nonmmy nibh euismod tincidunt ut laoreet dolore magna aliquam erat volutpat. Ut wisi enim ad minim veniam, quis nostrud exerci tationmcorper suscipit lobortis nisl ut aliquip ex ea commodo consequat. Duis autem vel eum iriure dolor in</p>
    </section>

    <p class="closing">Sincerely,</p>
    <div class="signature" role="img" aria-label="Handwritten signature of the sender"></div>

    <div class="footer-band" role="img" aria-label="Dark grey wave band along the foot of the page"></div>
  </main>
</body>
</html>
```